Quillmarsh Property Solutions need a business card design

Hello guys. We would need a business card design asap please.
We are a start up property investment business based in London UK specialised in buying, selling, managing and letting properties and helping distressed property owners.
The name of our Business is Quillmarsh, the logo symbolises the four fundamental elements of the world (earth, air, fire and water) and so it stands for strength, stability, longevity.
We would like the business card to communicate professionalism and reliability. Many many thanks indeed for your work.

Details:

1.) Rosalind Updike
Property Investor
Mobile: +44(0)7700123456
Email: rosalind.quillmarsh@mailbox-example.com

2.) Dominic Updike
Property Investor
Mobile: +44(0)7700987654
Email: dominic.quillmarsh@mailbox-example.com

```html
<!DOCTYPE html>
<html lang="en">
<head>
<meta charset="utf-8">
<title>Quillmarsh Property Solutions – Business Card</title>
<link rel="stylesheet" href="https://fonts.googleapis.com/css2?family=Open+Sans:wght@400;600;700;800&display=swap">
<style>
  :root {
    --canvas-bg: #e9e6e1;
    --card-white: #ffffff;
    --ink: #1b1b1b;
    --ink-soft: #555a60;
    --divider: #c9c9c9;
    --brand-green: #1fa64a;
    --brand-blue: #2a5cc4;
    --brand-red: #d8232f;
    --back-blue-light: #5b9ae8;
    --back-blue: #3a78d6;
    --back-blue-deep: #2c63c0;
    --on-dark: #ffffff;
  }
  * { box-sizing: border-box; margin: 0; padding: 0; }
  html, body {
    width: 1200px; height: 720px; overflow: hidden;
    background: var(--canvas-bg);
    font-family: "Open Sans", Arial, sans-serif;
  }
  .canvas { position: relative; width: 1200px; height: 720px; }
  .card {
    position: absolute; width: 540px; height: 309px;
    border-radius: 4px; overflow: hidden;
    box-shadow: 0 6px 18px rgba(0,0,0,0.18);
  }
  /* ---------- Front ---------- */
  .card-front { left: 40px; top: 205px; background: var(--card-white); }
  .card-front .swoosh { position: absolute; inset: 0; width: 100%; height: 100%; }
  .brand { position: absolute; left: 36px; top: 92px; }
  .brand-name {
    font-weight: 800; font-size: 27px; letter-spacing: 1px;
    color: var(--ink); text-transform: uppercase; line-height: 1;
  }
  .brand-tagline {
    margin-top: 4px; margin-left: 40px;
    font-weight: 700; font-size: 8.5px; letter-spacing: 0.6px;
    color: var(--ink); text-transform: uppercase;
  }
  .contact {
    position: absolute; left: 268px; top: 36px;
    padding-left: 14px; border-left: 1.5px solid var(--divider);
    font-size: 11px; color: var(--ink-soft); line-height: 1.9;
  }
  .contact-line { display: flex; align-items: center; gap: 7px; white-space: nowrap; }
  .contact-icon { width: 10px; height: 10px; flex: none; }
  .holder { position: absolute; left: 30px; bottom: 32px; color: var(--on-dark); }
  .holder-name { font-weight: 700; font-size: 19px; line-height: 1.1; }
  .holder-role { font-weight: 400; font-size: 12px; margin-top: 2px; }

  /* ---------- Back ---------- */
  .card-back {
    left: 620px; top: 205px;
    background: radial-gradient(ellipse at 55% 35%, var(--back-blue-light) 0%, var(--back-blue) 45%, var(--back-blue-deep) 100%);
    display: flex; flex-direction: column; align-items: center; justify-content: center;
    color: var(--on-dark);
  }
  .back-brand {
    display: flex; align-items: center; gap: 14px;
    font-weight: 800; font-size: 36px; letter-spacing: 2px; text-transform: uppercase;
  }
  .back-brand-mark { width: 22px; height: 22px; border-radius: 50%; background: var(--on-dark); }
  .back-url { margin-top: 58px; font-weight: 600; font-size: 15px; letter-spacing: 1.6px; }
</style>
</head>
<body>
<main class="canvas">

  <section class="card card-front" aria-label="Business card front">
    <svg class="swoosh" viewBox="0 0 540 309" preserveAspectRatio="none" aria-hidden="true">
      <path d="M0,214 C170,236 340,176 540,92 L540,309 L0,309 Z" fill="var(--brand-green)"/>
      <path d="M0,201 C170,223 340,163 540,79" fill="none" stroke="var(--brand-blue)" stroke-width="4"/>
      <path d="M250,177 C360,150 460,112 540,66 L540,73 C460,119 360,157 250,177 Z" fill="var(--brand-red)"/>
    </svg>

    <div class="brand">
      <div class="brand-name">Quillmarsh</div>
      <div class="brand-tagline">Property Solutions</div>
    </div>

    <div class="contact">
      <div class="contact-line">
        <svg class="contact-icon" viewBox="0 0 10 10" aria-hidden="true">
          <rect x="2.5" y="0.5" width="5" height="9" rx="1" fill="var(--brand-blue)"/>
          <rect x="3.4" y="1.6" width="3.2" height="5" fill="var(--card-white)"/>
        </svg>
        <span>+44(0)7700123456</span>
      </div>
      <div class="contact-line">
        <svg class="contact-icon" viewBox="0 0 10 10" aria-hidden="true">
          <rect x="0.5" y="2" width="9" height="6.5" rx="1" fill="var(--brand-blue)"/>
          <path d="M1,2.6 L5,5.6 L9,2.6" fill="none" stroke="var(--card-white)" stroke-width="0.9"/>
        </svg>
        <span>rosalind.quillmarsh@mailbox-example.com</span>
      </div>
    </div>

    <div class="holder">
      <div class="holder-name">Rosalind Updike</div>
      <div class="holder-role">Property Investor</div>
    </div>
  </section>

  <section class="card card-back" aria-label="Business card back">
    <div class="back-brand">
      <span class="back-brand-mark" aria-hidden="true"></span>
      <span>Quillmarsh</span>
    </div>
    <div class="back-url">www.quillmarsh-example.com</div>
  </section>

</main>
</body>
</html>
```